Venture 482 - Lumora Book Cover

I am looking for a Lumora book cover for my book about "Venture 482".
The Book is Titled:
Venture 482 Ascended
Shaping Outcomes: Paths To Unlocking Cosmic Truths
Author is Dorian Pell
Here is a book description that may help you understand more about it:
Inspired by the genius of Edwin Marlowe, this comprehensive guide delves into the ancient wisdom and cutting-edge science behind the 482 method, a powerful tool for manifesting your desires. Whether you're seeking personal growth, financial success, or spiritual enlightenment, this book provides advanced techniques and methods to transform your dreams into reality.
Any questions please ask.
Thanks
Owen

```html
<!DOCTYPE html>
<html lang="en">
<head>
<meta charset="utf-8">
<title>Venture 482 — Dorian Pell</title>
<link rel="stylesheet" href="https://fonts.googleapis.com/css2?family=Cinzel:wght@400;500&family=Cormorant+Garamond:wght@500&display=swap">
<style>
  :root {
    --backdrop: #d6d6d6;
    --night: #1e1a3a;
    --violet: #4a2a6b;
    --plum: #7a3f7e;
    --teal: #3f8f9e;
    --glow: #f2dca8;
    --gold: #ecc383;
    --gold-soft: #e3bf8c;
  }
  * { margin: 0; padding: 0; box-sizing: border-box; }
  html, body {
    width: 1200px;
    height: 1200px;
    overflow: hidden;
    background: var(--backdrop);
  }
  .cover {
    position: absolute;
    left: 258px;
    top: 54px;
    width: 684px;
    height: 1092px;
    overflow: hidden;
    background: var(--night);
  }
  .cover-art {
    position: absolute;
    inset: 0;
    background:
      radial-gradient(circle at 50% 47%, var(--glow) 0, rgba(242,220,168,0.7) 5%, rgba(236,195,131,0.35) 12%, transparent 22%),
      radial-gradient(circle at 50% 47%, transparent 26%, rgba(63,143,158,0.45) 30%, transparent 36%),
      radial-gradient(circle at 50% 47%, transparent 38%, rgba(236,195,131,0.35) 41%, transparent 45%),
      radial-gradient(ellipse at 50% 47%, transparent 48%, rgba(122,63,126,0.55) 55%, transparent 66%),
      radial-gradient(circle at 20% 82%, rgba(236,150,110,0.35) 0, transparent 22%),
      radial-gradient(circle at 85% 20%, rgba(63,143,158,0.35) 0, transparent 25%),
      linear-gradient(160deg, var(--violet) 0%, var(--night) 40%, var(--plum) 70%, var(--night) 100%);
  }
  .cover-text {
    position: absolute;
    inset: 0;
    color: var(--gold);
    text-align: center;
  }
  .subtitle {
    position: absolute;
    top: 222px;
    width: 100%;
    font-family: "Cinzel", serif;
    font-size: 15px;
    line-height: 27px;
    letter-spacing: 0.5px;
    color: var(--gold-soft);
  }
  .title {
    position: absolute;
    top: 300px;
    width: 100%;
    font-weight: 400;
  }
  .title-word {
    display: block;
    font-family: "Cinzel", serif;
    font-size: 76px;
    line-height: 90px;
    letter-spacing: 9px;
    padding-left: 9px;
  }
  .title-number {
    display: block;
    font-family: "Cormorant Garamond", serif;
    font-weight: 500;
    font-size: 168px;
    line-height: 140px;
  }
  .author {
    position: absolute;
    top: 940px;
    width: 100%;
    font-family: "Cinzel", serif;
    font-size: 40px;
    letter-spacing: 4px;
    padding-left: 4px;
  }
</style>
</head>
<body>
  <main class="cover">
    <div class="cover-art" role="img" aria-label="Glowing cosmic mandala of concentric golden and teal rings around a radiant star on a violet nebula background"></div>
    <div class="cover-text">
      <p class="subtitle">SHAPING OUTCOMES<br>PATHS TO UNLOCKING COSMIC TRUTHS</p>
      <h1 class="title">
        <span class="title-word">VENTURE</span>
        <span class="title-number">482</span>
      </h1>
      <p class="author">DORIAN PELL</p>
    </div>
  </main>
</body>
</html>
```